Spring Detox sale graphics for social media

You MUST read the Brief in the WORD document and follow the instructions there. I want to create 10 social media graphics (new Instagram size 4:5 (1080 x 1350 pixels) focusing on our Mother’s Day Spring Detox Sale graphics, using any of the pics attached. Use the attached pics, NO RANDOM STOCK PHOTOGRAPHY. For the color scheme of the graphics, they should all be complementary to the product colors or feel like Spring time.

Target Market(s)

primarily women

Requirements
Must have
• the photos and text attached

```html
<!DOCTYPE html>
<html lang="en">
<head>
<meta charset="utf-8">
<title>Mother's Day Spring Detox Sale</title>
<link rel="stylesheet" href="https://fonts.googleapis.com/css2?family=Montserrat:wght@400;700;800&family=Oswald:wght@400;500;600;700&display=swap">
<style>
  :root {
    --pink: #e0509a;
    --pink-soft: #f7c4de;
    --pink-mist: #fbe3ef;
    --plum: #66233f;
    --ink-green: #24382f;
    --white: #ffffff;
  }
  * { margin: 0; padding: 0; box-sizing: border-box; }
  html, body { width: 960px; height: 1200px; overflow: hidden; }
  body { font-family: "Montserrat", sans-serif; }
  .poster {
    position: relative;
    width: 960px;
    height: 1200px;
    overflow: hidden;
    background: linear-gradient(180deg, #ffffff 0%, #fff8fb 45%, var(--pink-mist) 70%, var(--pink-soft) 100%);
  }
  .waves { position: absolute; left: 0; top: 0; width: 960px; height: 1200px; }
  .eyebrow {
    position: absolute; left: 0; right: 0; top: 24px;
    text-align: center;
    font-family: "Montserrat", sans-serif; font-weight: 400;
    font-size: 44px; letter-spacing: 7px;
    color: var(--plum);
  }
  .headline {
    position: absolute; left: 0; right: 0; top: 74px;
    text-align: center;
    font-family: "Oswald", sans-serif; font-weight: 600;
    font-size: 64px; letter-spacing: 6px; line-height: 1;
    color: var(--pink);
  }
  .discount-number {
    position: absolute; left: 140px; top: 136px;
    font-family: "Montserrat", sans-serif; font-weight: 800;
    font-size: 380px; line-height: 1; letter-spacing: -16px;
    color: var(--pink);
    text-shadow: -6px -6px 0 var(--white), 4px 6px 10px rgba(102,35,63,0.18);
  }
  .discount-percent {
    position: absolute; left: 652px; top: 166px;
    font-family: "Oswald", sans-serif; font-weight: 400;
    font-size: 190px; line-height: 1;
    color: var(--pink);
    text-shadow: -4px -4px 0 var(--white), 3px 4px 8px rgba(102,35,63,0.15);
  }
  .discount-off {
    position: absolute; left: 656px; top: 354px;
    font-family: "Oswald", sans-serif; font-weight: 500;
    font-size: 112px; line-height: 1;
    color: var(--pink);
    text-shadow: -4px -4px 0 var(--white), 3px 4px 8px rgba(102,35,63,0.15);
  }
  .everything {
    position: absolute; left: 0; right: 0; top: 500px;
    text-align: center;
    font-family: "Oswald", sans-serif; font-weight: 700;
    font-size: 112px; line-height: 1.05;
    color: var(--plum);
    text-shadow: 3px 4px 6px rgba(102,35,63,0.2);
  }
  .shop-button {
    position: absolute; left: 260px; top: 627px;
    width: 442px; height: 84px; border-radius: 42px;
    background: var(--plum);
    color: var(--white);
    font-family: "Oswald", sans-serif; font-weight: 600;
    font-size: 70px; line-height: 84px; letter-spacing: 2px;
    text-align: center;
  }
  .podium { position: absolute; left: 0; top: 990px; width: 960px; height: 210px; }
  .product-lineup {
    position: absolute; left: 104px; top: 746px;
    width: 754px; height: 322px;
    border-radius: 18px;
    background: linear-gradient(90deg, #efe6ec 0%, #fbe0ea 30%, #e3f3ee 60%, #e4e8f6 100%);
  }
  .tagline {
    position: absolute; left: 0; right: 0; top: 1117px;
    text-align: center;
    font-family: "Montserrat", sans-serif; font-weight: 400;
    font-size: 32px; letter-spacing: 3px;
    color: var(--ink-green);
  }
  .tagline .accent { color: var(--pink); }
</style>
</head>
<body>
  <main class="poster">
    <svg class="waves" viewBox="0 0 960 1200" aria-hidden="true">
      <path d="M0 880 C200 820 380 900 560 840 C720 790 860 800 960 760 L960 1200 L0 1200 Z" fill="#f9d3e6" opacity="0.6"/>
      <path d="M0 960 C220 900 420 980 640 920 C780 880 880 900 960 870 L960 1200 L0 1200 Z" fill="#f4b4d4" opacity="0.55"/>
      <path d="M0 1080 C180 1050 300 1130 480 1120 C650 1110 800 1060 960 1080 L960 1200 L0 1200 Z" fill="#ee9cc6" opacity="0.5"/>
    </svg>

    <p class="eyebrow">MOTHER’S DAY</p>
    <h1 class="headline">SPRING DETOX SALE</h1>

    <div class="discount-number">25</div>
    <div class="discount-percent">%</div>
    <div class="discount-off">OFF</div>

    <h2 class="everything">EVERYTHING!</h2>
    <div class="shop-button">SHOP NOW!</div>

    <svg class="podium" viewBox="0 0 960 210" aria-hidden="true">
      <ellipse cx="483" cy="112" rx="441" ry="80" fill="#ffffff"/>
      <path d="M42 112 A441 80 0 0 0 924 112 L924 140 A441 80 0 0 1 42 140 Z" fill="#f1e6ec"/>
    </svg>

    <div class="product-lineup" role="img" aria-label="Product photo: four white supplement bottles with pink, red, green and blue labels standing in a row on a white podium"></div>

    <p class="tagline">Detox. Reset. <span class="accent">Feel Amazing.</span></p>
  </main>
</body>
</html>
```